Design a New Business Card for Our Company

We are looking for fresh, unique, and a modern business card that reflects our roots as digital marketing agency focused on SEM.

Industry/Entity Type

Marketing

Contact Information for Business Card

looking for very unique out of the box designs. clean and modern that compliments our logo

Requirements
Must have
• colors should match our logo
• Front should have name, address, email, and phone/fax of the person, phone/fax are the same number
• back should have our url

```html
<!DOCTYPE html>
<html lang="en">
<head>
<meta charset="utf-8">
<title>Northpeak Media – Business Card</title>
<link href="https://fonts.googleapis.com/css2?family=Arimo:wght@400;700&display=swap" rel="stylesheet">
<style>
  :root{
    --page:#e9ebee;
    --card-white:#fbfbfc;
    --ink-grey:#8f9296;
    --ink-soft:#a9acb0;
    --brand-blue:#4f8fc6;
    --blue-light:#7fb6dc;
    --blue-deep:#2f6fae;
    --tab-grey:#c9cbce;
    --rule:#c3c6ca;
    --white:#ffffff;
  }
  *{box-sizing:border-box;margin:0;padding:0}
  html,body{width:1200px;height:780px;overflow:hidden;background:var(--page);font-family:"Arimo",Arial,sans-serif}
  .stage{width:1200px;height:780px;display:flex;align-items:center;justify-content:center;gap:40px}
  .card{position:relative;width:540px;height:310px;border-radius:14px;overflow:hidden;box-shadow:0 6px 18px rgba(0,0,0,.18)}

  /* front */
  .card-front{background:var(--card-white)}
  .brand{position:absolute;display:flex;align-items:center;gap:10px;font-weight:700;letter-spacing:-.5px}
  .card-front .brand{left:38px;top:96px;color:var(--ink-grey);font-size:34px}
  .brand-dot{width:22px;height:22px;border-radius:50%;background:var(--brand-blue);flex:none}
  .address{position:absolute;right:34px;top:28px;text-align:right;color:var(--ink-soft);font-size:12px;line-height:1.45}
  .person{position:absolute;right:34px;top:110px;text-align:right}
  .person-name{color:var(--brand-blue);font-weight:700;font-size:16px;letter-spacing:.3px}
  .person-role{color:var(--ink-soft);font-size:11px;margin-top:2px}
  .person-lines{margin-top:12px}
  .contact-line{display:flex;align-items:center;justify-content:flex-end;gap:6px;color:var(--ink-grey);font-size:12px;line-height:1;margin-top:5px}
  .left-contacts{position:absolute;left:38px;top:200px}
  .left-contacts .contact-line{justify-content:flex-start;margin-top:6px}
  .icon{width:15px;height:15px;flex:none}
  .divider{position:absolute;left:38px;top:190px;width:250px;height:1px;background:var(--rule)}
  .front-band{position:absolute;left:0;bottom:0;width:100%;height:26px}
  .band-url{position:absolute;right:30px;bottom:6px;color:var(--white);font-size:12px;letter-spacing:.3px}

  /* back */
  .card-back{background:radial-gradient(circle at 55% 40%,var(--blue-light) 0%,var(--brand-blue) 55%,var(--blue-deep) 100%)}
  .back-pattern{position:absolute;inset:0 0 44px 0}
  .card-back .brand{left:50%;top:104px;transform:translateX(-50%);color:var(--white);font-size:44px;white-space:nowrap}
  .card-back .brand-dot{background:var(--white);width:26px;height:26px}
  .back-strip{position:absolute;left:0;bottom:0;width:100%;height:44px}
  .back-url{position:absolute;left:30px;bottom:14px;color:var(--blue-deep);font-size:12px;letter-spacing:.3px}
</style>
</head>
<body>
<main class="stage">

  <section class="card card-front" aria-label="Business card front">
    <div class="brand"><span class="brand-dot"></span>Northpeak Media</div>

    <p class="address">48 Harbor Lane, Suite 2<br>Millbrook, TX 75001</p>

    <div class="person">
      <p class="person-name">DANIEL REYES</p>
      <p class="person-role">Manager</p>
      <div class="person-lines">
        <p class="contact-line">555 210 4836
          <svg class="icon" viewBox="0 0 16 16"><rect width="16" height="16" rx="3" fill="#4f8fc6"/><path d="M5 3.5l2 2-1 1.2c.6 1.3 1.6 2.3 2.9 2.9l1.2-1 2 2-1.3 1.6C7.6 12 4 8.4 3.7 4.8z" fill="#fff"/></svg>
        </p>
        <p class="contact-line">555 210 4836
          <svg class="icon" viewBox="0 0 16 16"><rect width="16" height="16" rx="3" fill="#4f8fc6"/><rect x="4" y="3" width="8" height="4" fill="#fff"/><rect x="3" y="7" width="10" height="6" rx="1" fill="#fff"/><rect x="5" y="9" width="6" height="1.2" fill="#4f8fc6"/></svg>
        </p>
      </div>
    </div>

    <div class="divider"></div>

    <div class="left-contacts">
      <p class="contact-line">
        <svg class="icon" viewBox="0 0 16 16"><rect width="16" height="16" rx="3" fill="#4f8fc6"/><path d="M5 3.5l2 2-1 1.2c.6 1.3 1.6 2.3 2.9 2.9l1.2-1 2 2-1.3 1.6C7.6 12 4 8.4 3.7 4.8z" fill="#fff"/></svg>
        555 210 4836</p>
      <p class="contact-line">
        <svg class="icon" viewBox="0 0 16 16"><rect width="16" height="16" rx="3" fill="#4f8fc6"/><rect x="4" y="3" width="8" height="4" fill="#fff"/><rect x="3" y="7" width="10" height="6" rx="1" fill="#fff"/><rect x="5" y="9" width="6" height="1.2" fill="#4f8fc6"/></svg>
        555 210 4836</p>
      <p class="contact-line">
        <svg class="icon" viewBox="0 0 16 16"><rect width="16" height="16" rx="3" fill="#4f8fc6"/><rect x="3" y="4.5" width="10" height="7" fill="#fff"/><path d="M3 4.5l5 4 5-4" fill="none" stroke="#4f8fc6" stroke-width="1.2"/></svg>
        hello@northpeakmedia.com</p>
    </div>

    <svg class="front-band" viewBox="0 0 540 26" preserveAspectRatio="none" aria-hidden="true">
      <rect x="0" y="18" width="540" height="8" fill="#7fb6dc"/>
      <polygon points="250,26 262,4 345,4 345,26" fill="#c9cbce"/>
      <rect x="345" y="0" width="195" height="26" fill="#4f8fc6"/>
    </svg>
    <p class="band-url">www.northpeakmedia.com</p>
  </section>

  <section class="card card-back" aria-label="Business card back">
    <div class="back-pattern" role="img" aria-label="Soft pattern of large faint circles on blue"></div>
    <div class="brand"><span class="brand-dot"></span>Northpeak Media</div>
    <svg class="back-strip" viewBox="0 0 540 44" preserveAspectRatio="none" aria-hidden="true">
      <rect x="0" y="0" width="540" height="44" fill="#f6f7f8"/>
      <polygon points="300,44 300,10 318,0 392,0 392,44" fill="#c9cbce"/>
      <rect x="392" y="0" width="148" height="44" fill="#4f8fc6"/>
      <rect x="0" y="0" width="540" height="2" fill="#7fb6dc"/>
    </svg>
    <p class="back-url">www.northpeakmedia.com</p>
  </section>

</main>
</body>
</html>
```